Harborlight Amusement Collective (HAC)

We need a business card design for Harborlight Amusement Collective. Modern and sleek looking, with all critical information. Open to single or double sided designs, if double sided info needs to be all on one side. The main Logo is Harborlight Amusement collective and must be on the card. The other three logos are for the brands that fall under the group, they might be good on the back.

Industry/Entity Type

Business

```html
<!DOCTYPE html>
<html lang="en">
<head>
<meta charset="utf-8">
<title>Harborlight Amusement Collective — Business Card</title>
<link rel="stylesheet" href="https://fonts.googleapis.com/css2?family=Barlow+Semi+Condensed:wght@500&family=Montserrat:wght@400;500;600&display=swap">
<style>
  :root {
    --brand-blue: #2b5a9e;
    --brand-green: #7aa43a;
    --card-surface: #eef0f1;
    --page-bg: #d9dcdf;
    --ink: #1f2226;
    --band-text: #e9ecef;
  }
  * { margin: 0; padding: 0; box-sizing: border-box; }
  html, body { width: 1200px; height: 1054px; overflow: hidden; }
  body {
    background: var(--page-bg);
    font-family: "Montserrat", Arial, sans-serif;
    color: var(--ink);
  }
  .business-card {
    position: absolute;
    left: 100px;
    top: 224px;
    width: 1000px;
    height: 605px;
    background: var(--card-surface);
    overflow: hidden;
    box-shadow: 0 10px 30px rgba(0,0,0,0.18);
  }
  .header-band {
    position: absolute;
    left: 0; top: 0;
    width: 100%;
    height: 150px;
    background: var(--brand-blue);
  }
  .accent-rule {
    position: absolute;
    left: 0; top: 158px;
    width: 100%;
    height: 8px;
    background: var(--brand-green);
  }
  .holder {
    position: absolute;
    right: 51px;
    top: 38px;
    text-align: right;
    color: var(--band-text);
  }
  .holder-name {
    font-family: "Barlow Semi Condensed", "Arial Narrow", sans-serif;
    font-weight: 500;
    font-size: 40px;
    line-height: 1.1;
  }
  .holder-title {
    font-size: 21px;
    font-weight: 400;
    margin-top: 6px;
    letter-spacing: 0.3px;
  }
  .brand-mark {
    position: absolute;
    left: 237px;
    top: 200px;
    width: 112px;
    height: 112px;
    background: var(--brand-blue);
  }
  .brand-name {
    position: absolute;
    left: 34px;
    top: 340px;
    width: 518px;
    text-align: center;
    color: var(--brand-blue);
    font-weight: 600;
    font-size: 31px;
    line-height: 1.3;
    text-transform: uppercase;
  }
  .brand-name .line-two { display: block; letter-spacing: 10px; font-size: 29px; }
  .address {
    position: absolute;
    left: 54px;
    top: 490px;
    font-size: 23px;
    line-height: 41px;
    font-style: normal;
  }
  .contact-list {
    position: absolute;
    right: 56px;
    top: 456px;
    list-style: none;
    font-size: 23px;
    line-height: 38px;
    text-align: right;
  }
  .contact-list li { display: flex; justify-content: flex-end; align-items: center; gap: 14px; }
  .contact-list .web-domain { color: var(--brand-blue); }
  .contact-icon { width: 20px; height: 20px; fill: var(--brand-blue); flex: none; }
</style>
</head>
<body>
  <section class="business-card" aria-label="Harborlight Amusement Collective business card">
    <div class="header-band" aria-hidden="true"></div>
    <div class="accent-rule" aria-hidden="true"></div>

    <div class="holder">
      <p class="holder-name">Marcus Hale Bennett</p>
      <p class="holder-title">Managing Director</p>
    </div>

    <div class="brand-mark" aria-hidden="true"></div>
    <h1 class="brand-name">Harborlight Amusement <span class="line-two">Collective</span></h1>

    <address class="address">
      58 Quayside Rd.,<br>
      Port Elm, US 204817
    </address>

    <ul class="contact-list">
      <li>555.210.4837
        <svg class="contact-icon" viewBox="0 0 24 24" aria-hidden="true"><path d="M6.6 10.8c1.4 2.8 3.8 5.1 6.6 6.6l2.2-2.2c.3-.3.7-.4 1-.2 1.1.4 2.3.6 3.6.6.6 0 1 .4 1 1V20c0 .6-.4 1-1 1C10.6 21 3 13.4 3 4c0-.6.4-1 1-1h3.5c.6 0 1 .4 1 1 0 1.3.2 2.5.6 3.6.1.3 0 .7-.2 1z"/></svg>
      </li>
      <li>mbennett@harborlightfun.com
        <svg class="contact-icon" viewBox="0 0 24 24" aria-hidden="true"><path d="M2 5h20v14H2z M4 7v.5l8 5.5 8-5.5V7l-8 5.2z" fill-rule="evenodd"/></svg>
      </li>
      <li><span>www.<span class="web-domain">harborlightfun</span>.com</span>
        <svg class="contact-icon" viewBox="0 0 24 24" aria-hidden="true"><path d="M12 2a10 10 0 1 0 0 20 10 10 0 0 0 0-20zm6.9 6h-2.9a15.7 15.7 0 0 0-1.4-3.6A8 8 0 0 1 18.9 8zM12 4c.8 1.2 1.5 2.5 1.9 4h-3.8c.4-1.5 1.1-2.8 1.9-4zM4.3 14a8 8 0 0 1 0-4h3.4a16 16 0 0 0 0 4zm.8 2h2.9c.3 1.3.8 2.5 1.4 3.6A8 8 0 0 1 5.1 16zM8 8H5.1a8 8 0 0 1 4.3-3.6C8.8 5.5 8.300 6.7 8 8zm4 12c-.8-1.2-1.5-2.5-1.9-4h3.8c-.4 1.5-1.1 2.8-1.9 4zm2.3-6H9.7a14.6 14.6 0 0 1 0-4h4.6a14.6 14.6 0 0 1 0 4zm.3 5.6c.6-1.1 1.1-2.3 1.4-3.6h2.9a8 8 0 0 1-4.3 3.6zm1.7-5.6a16 16 0 0 0 0-4h3.4a8 8 0 0 1 0 4z"/></svg>
      </li>
    </ul>
  </section>
</body>
</html>
```